Sophisticated, clean website reflecting my feminine, playful side to sell my abstract art,

I need a website no more than 3 pages to showcase my paintings, a little about me and some contact info. I do abstracts so looking for something a little edgy, yet feminine and current.
Updates

Hi there, These are some artists websites that I Iike: Marnelvoss.com (I like how airy it is) peterwallombry.com garethpolvens.com (I like how it scrolls) I'll need a place for a photo ( a headshot-i do not have it yet so I'll need to be able to upload that later) as well as an area for my bio. Also, it's important that I will be able to upload any new photos and descriptions easily so it should be user friendly. Lastly, I like in a sunny place so would like to have this seem upbeat and playful as that is how i like to paint. thanks-I'm trying to upload my photos now -

Target Market(s)

ppl ages 35-70 who want large scale art for their homes

Industry/Entity Type

art

Coding

Coded - Design and coding required

Number of Pages Required

3 page

Colors

Designer to choose colors to be used in the design.

Requirements
Must have
• photos of my art, a place for my bio, be easy to reach me. tasteful-nothing too "in your face" -my clients are pretty high end and organized. They like clean lines
Nice to have
• sophisticated background, muted tones in the back-similar clean font throughout-no cursive
Should not have
• too many dark areas. Too many blocks of color. Too serious.

```html
<!DOCTYPE html>
<html lang="en">
<head>
<meta charset="utf-8">
<title>Your Name — Art Gallery</title>
<link rel="stylesheet" href="https://fonts.googleapis.com/css2?family=Playfair+Display:wght@400;500&family=Source+Sans+3:wght@400;600;700&display=swap">
<style>
:root{
  --plum:#7e6592;
  --lilac:#d6bdd4;
  --lilac-band:#d4bcd6;
  --lilac-about:#cfaac9;
  --ink:#1a1a1a;
  --white:#ffffff;
  --card:#faf7fc;
  --gold:#f2c500;
  --accent-a:#b99c3e;
  --accent-b:#8f78a3;
  --grey:#cfcfcf;
}
*{box-sizing:border-box;margin:0;padding:0}
html,body{width:1200px;height:4992px;overflow:hidden}
body{position:relative;background:var(--white);font-family:"Source Sans 3",Arial,sans-serif;color:var(--ink)}
.abs{position:absolute}
.serif{font-family:"Playfair Display",Georgia,serif;font-weight:400}

/* top bar */
.topbar{left:0;top:0;width:1200px;height:35px;background:var(--plum);color:var(--white);font-size:11px}
.social-mini{left:101px;top:9px;display:flex;gap:10px}
.social-mini span{display:flex;align-items:center;gap:4px}
.dot{width:12px;height:12px;border:1.5px solid var(--white);border-radius:50%;display:inline-block}
.contact-mini{right:101px;top:8px;display:flex;gap:26px;align-items:center}
.contact-mini span{display:flex;align-items:center;gap:8px}

/* nav */
.brand{left:101px;top:56px;font-size:32px}
.nav{left:373px;top:68px;display:flex;gap:22px;font-size:10px;font-weight:600}
.nav .active{color:var(--plum)}
.nav-icons{left:822px;top:59px;display:flex;gap:13px}
.icon-btn{width:32px;height:32px;border:1.5px solid var(--plum);border-radius:50%;display:flex;align-items:center;justify-content:center}
.btn{display:flex;align-items:center;justify-content:center;font-weight:700;font-size:14px;color:var(--white)}
.btn-plum{background:var(--plum)}
.btn-black{background:#000}
.login{left:973px;top:52px;width:126px;height:47px;font-size:15px}

/* hero */
.hero-art{left:0;top:112px;width:620px;height:479px;background:radial-gradient(circle at 40% 55%,#2c2136 0,#5c4278 18%,#9b82b5 38%,#d9d2dc 62%,#efece9 100%)}
.hero-panel{left:520px;top:153px;width:680px;height:477px;background:var(--lilac)}
.hero-title{left:647px;top:228px;font-size:50px;line-height:1.2;color:var(--ink)}
.hero-text{left:647px;top:374px;width:420px;font-size:14px;line-height:1.55}
.explore{left:647px;top:461px;width:188px;height:51px}

/* section heading with accent placeholder */
.sec-head{left:0;width:1200px;text-align:center}
.title-wrap{display:inline-block;position:relative}
.sec-title{font-size:36px;line-height:1.2}
.accent{position:absolute;left:100%;top:-8px;margin-left:6px;width:56px;height:56px;border-radius:4px;background:linear-gradient(135deg,var(--accent-a),var(--accent-b));opacity:.55}
.hero-accent{left:1085px;top:232px;width:56px;height:56px;border-radius:4px;background:linear-gradient(135deg,var(--accent-a),var(--accent-b));opacity:.55}

/* featured */
.card-img{width:308px;height:269px}
.stars{font-size:18px;letter-spacing:2px;color:var(--gold);text-align:center;width:308px}
.stars .off{color:var(--grey)}
.price{width:308px;text-align:center;color:var(--plum);font-weight:700;font-size:21px}
.pname{width:308px;text-align:center;font-weight:600;font-size:21px}
.buy{width:174px;height:48px}
.sq{width:48px;height:48px;border:1.5px solid var(--plum);display:flex;align-items:center;justify-content:center}

/* gallery */
.gallery{left:0;top:1382px;width:1200px;height:973px;background:linear-gradient(120deg,var(--lilac-band),#dcc6dd 50%,var(--lilac-band))}
.tile{width:320px;height:272px}

/* reviews */
.review{width:462px;height:204px;background:var(--card);border-left:4px solid var(--plum);border-bottom:4px solid var(--plum);border-top:1px solid #e5dcea;border-right:1px solid #e5dcea;padding:30px 24px 0 26px;font-size:14px;line-height:1.6}
.avatar{width:64px;height:64px;border-radius:50%;background:linear-gradient(#b9b2ad,#8c837e)}
.rname{font-weight:700;font-size:13px}
.rsub{font-size:14px}
.rstars{color:var(--gold);font-size:20px;letter-spacing:2px}

/* about */
.about-photo{left:0;top:3001px;width:594px;height:605px;background:linear-gradient(135deg,#e7c6d6,#c9a1c2 40%,#efe3e4 70%,#d38fb6)}
.about-panel{left:594px;top:3001px;width:606px;height:605px;background:var(--lilac-about)}
.about-head{left:661px;top:3088px}
.about-text{left:661px;top:3196px;width:432px;font-size:13.5px;line-height:1.65}

/* contact */
.touch{left:0;top:3606px;width:1200px;height:320px;background:linear-gradient(90deg,#7a6290,var(--plum) 50%,#866d98)}
.touch-title{color:var(--white)}
.form{left:227px;top:3790px;width:744px;height:74px;background:var(--white);border:1px solid #e8e0ee}
.email{left:30px;top:28px;font-size:11px}
.signup{left:527px;top:13px;width:188px;height:48px}

/* feed */
.insta{width:240px;height:210px}
.follow{left:506px;top:4618px;width:186px;height:48px}

/* footer */
.footer{left:0;top:4763px;width:1200px;height:151px;background:var(--plum);color:var(--white)}
.foot-icons{left:101px;top:56px;display:flex;gap:10px}
.foot-icons .ci{min-width:34px;height:34px;border:1.5px solid var(--white);border-radius:17px;display:flex;align-items:center;justify-content:center;font-size:10px;font-weight:600;padding:0 6px}
.foot-links{right:101px;top:63px;display:flex;gap:24px;font-size:14px;font-weight:600}
.legal{top:4946px;font-size:10px}
</style>
</head>
<body>

<!-- top bar -->
<div class="abs topbar">
  <div class="abs social-mini"><span><i class="dot"></i>Pinora</span><span><i class="dot"></i>Workly</span><span><i class="dot"></i>Friendo</span></div>
  <div class="abs contact-mini">
    <span><svg width="18" height="18" viewBox="0 0 18 18"><circle cx="9" cy="9" r="8" fill="none" stroke="#fff" stroke-width="1.3"/><rect x="5" y="6" width="8" height="6" fill="none" stroke="#fff"/><path d="M5 6l4 3 4-3" fill="none" stroke="#fff"/></svg>hello@yournamestudio.art</span>
    <span><svg width="18" height="18" viewBox="0 0 18 18"><circle cx="9" cy="9" r="8" fill="none" stroke="#fff" stroke-width="1.3"/><path d="M6 5c0 4 3 7 7 7l-1-2-2 1-3-3 1-2z" fill="#fff"/></svg>123-456-7890</span>
  </div>
</div>

<!-- nav -->
<div class="abs brand serif">Your Name</div>
<nav class="abs nav"><span class="active">Home</span><span>Featured Collection</span><span>Reviews</span><span>Art Gallery</span><span>About The Artist</span></nav>
<div class="abs nav-icons">
  <div class="icon-btn"><svg width="14" height="14" viewBox="0 0 14 14"><circle cx="7" cy="4" r="3" fill="#7e6592"/><path d="M1 13c0-4 3-5 6-5s6 1 6 5z" fill="#7e6592"/></svg></div>
  <div class="icon-btn"><svg width="14" height="14" viewBox="0 0 24 24"><path d="M12 21l-8-8a5 5 0 017-7l1 1 1-1a5 5 0 017 7z" fill="none" stroke="#7e6592" stroke-width="2"/></svg></div>
  <div class="icon-btn"><svg width="15" height="15" viewBox="0 0 24 24"><path d="M2 3h3l3 12h11l2-8H7" fill="none" stroke="#7e6592" stroke-width="2"/><circle cx="9" cy="20" r="1.6" fill="#7e6592"/><circle cx="18" cy="20" r="1.6" fill="#7e6592"/></svg></div>
</div>
<div class="abs btn btn-plum login">Login</div>

<!-- hero -->
<div class="abs hero-art" role="img" aria-label="Abstract painting in purples and black with burst shapes"></div>
<div class="abs hero-panel"></div>
<h1 class="abs hero-title serif">Welcome To My Art<br>Gallery</h1>
<div class="abs hero-accent" role="img" aria-label="Paintbrush accent"></div>
<p class="abs hero-text">Lorem ipsum dolor sit amet, consectetur adipiscing elit. Nibh sit nascetur pulvinar risus aliquet sed facilisis.</p>
<div class="abs btn btn-black explore">Explore All</div>

<!-- featured -->
<div class="abs sec-head" style="top:722px"><div class="title-wrap"><h2 class="sec-title serif">Featured Collection</h2><span class="accent" role="img" aria-label="Paintbrush accent"></span></div></div>

<div class="abs card-img" style="left:101px;top:832px;background:radial-gradient(circle at 45% 60%,#f2efe6,#4a8f8a 30%,#c46a2a 55%,#2f4f63 80%)" role="img" aria-label="Abstract painting in teal and orange"></div>
<div class="abs card-img" style="left:446px;top:832px;background:linear-gradient(90deg,#1d8c84 0,#e7e1d4 15%,#dcd5c8 60%,#1f3c88 75%,#1a347d)" role="img" aria-label="Abstract painting in cream and deep blue"></div>
<div class="abs card-img" style="left:791px;top:832px;background:linear-gradient(180deg,#0f8a80 0,#0f8a80 82%,#c49a5c 82%)" role="img" aria-label="Abstract painting with teal stripe on wood"></div>

<div class="abs stars" style="left:101px;top:1116px">★★★★<span class="off">★</span></div>
<div class="abs stars" style="left:446px;top:1116px">★★★★<span class="off">★</span></div>
<div class="abs stars" style="left:791px;top:1116px">★★★★★</div>
<div class="abs price" style="left:101px;top:1151px">$50.00</div>
<div class="abs price" style="left:446px;top:1151px">$68.00</div>
<div class="abs price" style="left:791px;top:1151px">$75.90</div>
<div class="abs pname" style="left:101px;top:1192px">Coloured Painting</div>
<div class="abs pname" style="left:446px;top:1192px">Coloured Painting</div>
<div class="abs pname" style="left:791px;top:1192px">Coloured Painting</div>

<div class="abs btn btn-plum buy" style="left:103px;top:1241px">Buy Now</div>
<div class="abs sq" style="left:291px;top:1241px"><svg width="24" height="24" viewBox="0 0 24 24"><path d="M12 21l-8-8a5 5 0 017-7l1 1 1-1a5 5 0 017 7z" fill="none" stroke="#7e6592" stroke-width="1.6"/></svg></div>
<div class="abs sq" style="left:355px;top:1241px"><svg width="24" height="24" viewBox="0 0 24 24"><path d="M2 3h3l3 12h11l2-8H7" fill="none" stroke="#7e6592" stroke-width="1.8"/><circle cx="9" cy="20" r="1.6" fill="#7e6592"/><circle cx="18" cy="20" r="1.6" fill="#7e6592"/></svg></div>
<div class="abs btn btn-plum buy" style="left:448px;top:1241px">Buy Now</div>
<div class="abs sq" style="left:636px;top:1241px"><svg width="24" height="24" viewBox="0 0 24 24"><path d="M12 21l-8-8a5 5 0 017-7l1 1 1-1a5 5 0 017 7z" fill="none" stroke="#7e6592" stroke-width="1.6"/></svg></div>
<div class="abs sq" style="left:700px;top:1241px"><svg width="24" height="24" viewBox="0 0 24 24"><path d="M2 3h3l3 12h11l2-8H7" fill="none" stroke="#7e6592" stroke-width="1.8"/><circle cx="9" cy="20" r="1.6" fill="#7e6592"/><circle cx="18" cy="20" r="1.6" fill="#7e6592"/></svg></div>
<div class="abs btn btn-plum buy" style="left:793px;top:1241px">Buy Now</div>
<div class="abs sq" style="left:981px;top:1241px"><svg width="24" height="24" viewBox="0 0 24 24"><path d="M12 21l-8-8a5 5 0 017-7l1 1 1-1a5 5 0 017 7z" fill="none" stroke="#7e6592" stroke-width="1.6"/></svg></div>
<div class="abs sq" style="left:1045px;top:1241px"><svg width="24" height="24" viewBox="0 0 24 24"><path d="M2 3h3l3 12h11l2-8H7" fill="none" stroke="#7e6592" stroke-width="1.8"/><circle cx="9" cy="20" r="1.6" fill="#7e6592"/><circle cx="18" cy="20" r="1.6" fill="#7e6592"/></svg></div>

<!-- gallery -->
<section class="abs gallery"></section>
<div class="abs sec-head" style="top:1478px"><div class="title-wrap"><h2 class="sec-title serif">Art Gallery</h2><span class="accent" role="img" aria-label="Paintbrush accent"></span></div></div>
<div class="abs tile" style="left:101px;top:1586px;background:linear-gradient(90deg,#1d8c84,#e4ded2 20%,#d9d2c6 60%,#1f3c88 78%)" role="img" aria-label="Abstract painting in cream and blue"></div>
<div class="abs tile" style="left:440px;top:1586px;background:radial-gradient(circle at 40% 50%,#f1ece1,#d8a53a 35%,#3a5f9a 60%,#b8874f)" role="img" aria-label="Abstract painting with gold and blue swirls"></div>
<div class="abs tile" style="left:777px;top:1586px;background:linear-gradient(90deg,#9a6d3e 0,#9a6d3e 8%,#e6e4e0 8%,#8ec4d8 70%,#e8e6e2 92%,#9a6d3e 92%)" role="img" aria-label="Abstract painting with blue drips"></div>
<div class="abs tile" style="left:101px;top:1890px;background:radial-gradient(circle at 55% 55%,#f3e9d4,#e0a21c 35%,#b4491f 60%,#3a5a7a)" role="img" aria-label="Abstract painting in yellow and rust"></div>
<div class="abs tile" style="left:440px;top:1890px;background:radial-gradient(circle at 50% 50%,#e7f0dc,#5fb24b 35%,#1f7a3a 65%,#a97b4c)" role="img" aria-label="Abstract painting in greens"></div>
<div class="abs tile" style="left:777px;top:1890px;background:radial-gradient(circle at 40% 35%,#4a1c18,#7d3a2e 35%,#d8b0ac 65%,#f2eeec)" role="img" aria-label="Abstract painting in maroon and pink"></div>
<div class="abs btn btn-black" style="left:506px;top:2212px;width:188px;height:50px">View All</div>

<!-- reviews -->
<div class="abs sec-head" style="top:2450px"><div class="title-wrap"><h2 class="sec-title serif">Reviews</h2><span class="accent" role="img" aria-label="Paintbrush accent"></span></div></div>

<div class="abs review" style="left:116px;top:2575px">Lorem ipsum dolor sit amet, consectetur adipiscing elit. Habitasse pulvinar malesuada turpis ullamcorper. Etiam arcu elit euismod quisque. Pulvinar turpis pellentesque duis leo lectus turpis eu. Egestas netus fermentum vitae fusce porta. Vitae quam aliquam molestie commodo amet euismod. Cras in hendrerit congue viverra bibendum.</div>
<svg class="abs" style="left:180px;top:2775px" width="60" height="46" viewBox="0 0 60 46"><path d="M2 0v42L48 0" fill="#faf7fc" stroke="#7e6592" stroke-width="4"/></svg>
<div class="abs review" style="left:632px;top:2581px">Lorem ipsum dolor sit amet, consectetur adipiscing elit. Habitasse pulvinar malesuada turpis ullamcorper. Etiam arcu elit euismod quisque. Pulvinar turpis pellentesque duis leo lectus turpis eu. Egestas netus fermentum vitae fusce porta. Vitae quam aliquam molestie commodo amet euismod. Cras in hendrerit congue viverra bibendum.</div>
<svg class="abs" style="left:704px;top:2781px" width="60" height="46" viewBox="0 0 60 46"><path d="M2 0v42L48 0" fill="#faf7fc" stroke="#7e6592" stroke-width="4"/></svg>

<div class="abs avatar" style="left:172px;top:2843px" role="img" aria-label="Reviewer portrait"></div>
<div class="abs rname" style="left:254px;top:2855px">JASON MONA</div>
<div class="abs rsub" style="left:254px;top:2880px">Lorem ipsum dolor</div>
<div class="abs rstars" style="left:428px;top:2860px">★★★★★</div>
<div class="abs avatar" style="left:689px;top:2843px" role="img" aria-label="Reviewer portrait"></div>
<div class="abs rname" style="left:771px;top:2855px">JOHN DEO</div>
<div class="abs rsub" style="left:771px;top:2880px">Lorem ipsum dolor</div>
<div class="abs rstars" style="left:946px;top:2860px">★★★★★</div>

<!-- about -->
<div class="abs about-photo" role="img" aria-label="Photo of the artist painting outdoors among blossoms"></div>
<div class="abs about-panel"></div>
<div class="abs about-head"><div class="title-wrap"><h2 class="sec-title serif">About The Artist</h2><span class="accent" role="img" aria-label="Paintbrush accent"></span></div></div>
<p class="abs about-text">Lorem ipsum dolor sit amet, consectetur adipiscing elit. Consequat quis turpis adipiscing tincidunt. Fames ut lectus tempus quis lacus nunc arcu. Mi, ultrices varius ultrices massa aliquam odio enim quam. Quisque libero sed eget pellentesque imperdiet. At et lorem habitant amet morbi velit, sed eu lorem. Egestas egestas mattis ultrices aliquam. Malesuada at malesuada convallis feugiat. Pharetra venenatis odio duis quis semper amet. Amet justo, enim ac lacus, aenean elementum. Commodo fermentum viverra consectetur at elit mauris a orci. Quis molestie cursus nisi lorem mi.<br>Suscipit cursus sagittis odio ut sit in aliquam at amet. Leo orci sed mauris sit morbi mi diam vestibulum. Ultrices aliquam donec semper gravida nibh dictum dui. Suspendisse ultrices egestas dui a, faucibus. Eget a id placerat semper consectetur. Integer augue tortor etiam quis. Euismod imperdiet elit proin fames felis lectus justo.</p>

<!-- get in touch -->
<section class="abs touch"></section>
<div class="abs sec-head" style="top:3670px"><div class="title-wrap"><h2 class="sec-title serif touch-title">Get In Touch</h2><span class="accent" role="img" aria-label="Paintbrush accent"></span></div></div>
<div class="abs form">
  <span class="abs email">Email Address</span>
  <div class="abs btn btn-plum signup">Sign Up</div>
</div>

<!-- feed -->
<div class="abs sec-head" style="top:4022px"><div class="title-wrap"><h2 class="sec-title serif">Follow Me On Pinora</h2><span class="accent" role="img" aria-label="Paintbrush accent"></span></div></div>
<div class="abs insta" style="left:101px;top:4127px;background:radial-gradient(circle at 50% 50%,#3d2b5a,#8a6fb2 35%,#e6e0dc 70%)" role="img" aria-label="Purple abstract painting"></div>
<div class="abs insta" style="left:353px;top:4127px;background:radial-gradient(circle at 50% 50%,#7a1f14,#b54a32 35%,#efe6e0 70%,#b07a48)" role="img" aria-label="Red swirl painting"></div>
<div class="abs insta" style="left:605px;top:4127px;background:radial-gradient(circle at 50% 60%,#e8b8b8,#b56a70 35%,#3b2433 65%,#e7d4d2)" role="img" aria-label="Pink floral abstract"></div>
<div class="abs insta" style="left:857px;top:4127px;background:radial-gradient(circle at 50% 50%,#efc9c8,#c47a80 40%,#5a3a3f 70%,#e8d6d2)" role="img" aria-label="Pink floral abstract"></div>
<div class="abs insta" style="left:101px;top:4346px;background:radial-gradient(circle at 50% 50%,#e4efdc,#4fae4e 40%,#1a6e3c 70%,#9c7a52)" role="img" aria-label="Green abstract painting"></div>
<div class="abs insta" style="left:353px;top:4346px;background:linear-gradient(90deg,#1d8c84,#e4ded2 22%,#d9d2c6 60%,#1f3c88 78%)" role="img" aria-label="Cream and blue abstract"></div>
<div class="abs insta" style="left:605px;top:4346px;background:radial-gradient(circle at 45% 45%,#a8321f,#e9e1da 30%,#efeae4 55%,#a77a4e 80%)" role="img" aria-label="Red rose painting on wood"></div>
<div class="abs insta" style="left:857px;top:4346px;background:radial-gradient(circle at 50% 50%,#e4efdc,#4fae4e 40%,#1a6e3c 70%,#9c7a52)" role="img" aria-label="Green abstract painting"></div>
<div class="abs btn btn-black follow">Follow</div>

<!-- footer -->
<footer class="abs footer">
  <div class="abs foot-icons">
    <span class="ci">Pinora</span>
    <span class="ci">Workly</span>
    <span class="ci"><svg width="16" height="16" viewBox="0 0 18 18"><path d="M4 2c0 7 5 12 12 12l-1-3-3 1-5-5 1-3z" fill="none" stroke="#fff" stroke-width="1.5"/></svg></span>
    <span class="ci"><svg width="16" height="16" viewBox="0 0 18 18"><rect x="2" y="4" width="14" height="10" fill="none" stroke="#fff" stroke-width="1.5"/><path d="M2 4l7 6 7-6" fill="none" stroke="#fff" stroke-width="1.5"/></svg></span>
    <span class="ci">Friendo</span>
  </div>
  <nav class="abs foot-links"><span>Home</span><span>Featured Collection</span><span>Reviews</span><span>Art Gallery</span><span>About The Artist</span></nav>
</footer>
<div class="abs legal" style="left:101px">Terms Of Use</div>
<div class="abs legal" style="left:194px">Privacy Policy</div>
<div class="abs legal" style="right:101px">© 2022 Art Gallery. ALL RIGHTS RESERVED</div>

</body>
</html>
```